Every Shelf Set Neatly or ESN Organized needs a business card design. ESN Organized is a professi

We need a business card design that is clean, sharp and conveys a sense of organization. I already have a logo.

Target Market(s)

Families (specifically mothers), small business owners, parents, seniors

Industry/Entity Type

Business

Contact Information for Business Card

My website is www.esnorganized-example.com and my Facebook page is http://www.sociallink-example.com/everyshelfsetneatly. The phone number is 418-552-7094 and I want to be listed as Lorna M. Pelham, Owner

Requirements
Must have
• My logo.

```html
<!DOCTYPE html>
<html lang="en">
<head>
<meta charset="utf-8">
<title>ESN Organized – Business Card</title>
<link href="https://fonts.googleapis.com/css2?family=Montserrat:wght@300;400&display=swap" rel="stylesheet">
<style>
  :root {
    --backdrop: #232323;
    --brand-blue: #0078d4;
    --paper: #efefef;
    --ink: #000000;
    --light: #ffffff;
  }
  * { margin: 0; padding: 0; box-sizing: border-box; }
  html, body {
    width: 1200px; height: 840px; overflow: hidden;
    background: var(--backdrop);
    font-family: "Montserrat", Arial, sans-serif;
  }
  .canvas { position: relative; width: 1200px; height: 840px; }

  .card {
    position: absolute; width: 459px; height: 262px; overflow: hidden;
  }
  .card--front { left: 451px; top: 121px; display: flex; flex-direction: column; }
  .card--back { left: 318px; top: 442px; background: var(--brand-blue); }

  .name-band {
    height: 63px; background: var(--brand-blue); color: var(--light);
    text-align: center; padding-top: 11px;
  }
  .person-name { font-size: 19px; font-weight: 400; letter-spacing: 0.3px; line-height: 1.1; }
  .person-role { font-size: 13px; font-weight: 400; line-height: 1.2; }

  .logo-band {
    height: 125px; background: var(--paper);
    display: flex; align-items: center; justify-content: center;
  }
  .company-name {
    font-size: 27px; font-weight: 300; color: var(--ink);
    letter-spacing: 5px; white-space: nowrap;
  }

  .contact-band {
    flex: 1; background: var(--ink); color: var(--light);
    text-align: center; font-size: 13.5px; font-weight: 300;
    padding-top: 19px; line-height: 1.35;
  }
  .social-line { display: inline-flex; align-items: center; gap: 5px; }
  .social-mark { width: 11px; height: 11px; background: var(--light); display: inline-block; }

  .back-mark {
    position: absolute; left: 34px; bottom: 18px;
    font-size: 44px; font-weight: 300; color: var(--light); letter-spacing: 1px;
  }
</style>
</head>
<body>
<main class="canvas">
  <section class="card card--front" aria-label="Business card front">
    <header class="name-band">
      <p class="person-name">Lorna M. Pelham</p>
      <p class="person-role">Owner</p>
    </header>
    <div class="logo-band">
      <p class="company-name">ESN ORGANIZED</p>
    </div>
    <footer class="contact-band">
      <p>418-552-7094 &nbsp;|&nbsp; www.esnorganized-example.com</p>
      <p class="social-line"><span class="social-mark"></span>everyshelfsetneatly</p>
    </footer>
  </section>

  <section class="card card--back" aria-label="Business card back">
    <p class="back-mark">ESN</p>
  </section>
</main>
</body>
</html>
```